NEW Modern Sleek Business Card for VR Language Startup

Our startup is using VR to lead the next wave of world language education. We need a two-sided business card that introduces the larger organization (Brightloom Language Inc) and our contact info on one side and shows the product, Glimwoorld, on the other side.

Side 1 (contact info)= Brightloom Logo and Contact info (name, title, phone, email)

Side 2 (product)= Glimworld logo, text, and website
Text= Culturally Immersive Language Learning Games
Website= www.glimworld-play.com

Target Market(s)

Education, Technology

Contact Information for Business Card

Contact info will be updated upon approval of the design. For now, put this as a placeholder.

Perry Dunmore
Founder & CEO
pdunmore@quillpost-mail.net
(555)-014-2286

Font styles to use
Other font styles liked:
• Gibson and Century Gothic are the brand fonts

Requirements
Nice to have
• I would love to see cohesion between the design and colors of the two logos. I have attached a few business card designs that I like, so you can get a feel for my preferred style.

```html
<!DOCTYPE html>
<html lang="en">
<head>
<meta charset="utf-8">
<title>Brightloom Language Inc – Business Card</title>
<link href="https://fonts.googleapis.com/css2?family=Montserrat:wght@600&family=Roboto:ital,wght@0,400;0,500;1,500&display=swap" rel="stylesheet">
<style>
  :root {
    --canvas: #e4e4e4;
    --card-white: #ffffff;
    --card-dark: #232526;
    --pattern-dark: #2a3234;
    --ink: #1f1f1f;
    --ink-soft: #555a5e;
    --name-blue: #3fa9f5;
    --title-orange: #f7883b;
    --rule: #c8c8c8;
    --band-black: #1b1b1b;
    --accent-blue: #4a7bf0;
    --mark-orange: #f7883b;
    --mark-purple: #8a5cf6;
    --mark-cyan: #2ad4ea;
    --white: #ffffff;
  }
  * { box-sizing: border-box; margin: 0; padding: 0; }
  html, body { width: 1200px; height: 1200px; overflow: hidden; }
  body { background: var(--canvas); position: relative; font-family: "Roboto", sans-serif; }

  .card {
    position: absolute;
    left: 257px;
    width: 686px;
    height: 392px;
    overflow: hidden;
    box-shadow: 0 18px 30px rgba(0,0,0,.18);
  }
  .card--front { top: 165px; background: var(--card-white); }
  .card--back { top: 653px; background: var(--card-dark); }

  /* Front */
  .brand {
    position: absolute;
    left: 60px;
    top: 106px;
    width: 260px;
    text-align: center;
  }
  .brand__dot {
    display: block;
    width: 78px; height: 78px;
    margin: 0 auto 22px;
    border-radius: 50%;
    background: linear-gradient(160deg, var(--mark-orange), var(--mark-purple) 55%, var(--mark-cyan));
  }
  .brand__name {
    font-family: "Montserrat", sans-serif;
    font-weight: 600;
    font-size: 30px;
    letter-spacing: 3px;
    color: var(--ink);
  }
  .divider {
    position: absolute;
    left: 343px; top: 105px;
    width: 2px; height: 158px;
    background: linear-gradient(var(--card-white), var(--rule) 20%, var(--rule) 80%, var(--card-white));
  }
  .contact { position: absolute; left: 375px; top: 130px; }
  .contact__name { font-weight: 500; font-size: 27px; color: var(--name-blue); line-height: 1; }
  .contact__title { font-size: 18px; color: var(--title-orange); margin-top: 4px; }
  .contact__list { list-style: none; margin-top: 18px; }
  .contact__item {
    display: flex; align-items: center; gap: 9px;
    font-size: 16.5px; color: var(--ink-soft); line-height: 23px;
  }
  .contact__icon { width: 15px; height: 15px; fill: var(--ink); flex: none; }

  .color-band { position: absolute; left: 0; bottom: 0; width: 100%; height: 11px; }

  /* Back */
  .pattern {
    position: absolute; inset: 0;
    background: radial-gradient(circle at 50% 45%, var(--pattern-dark), var(--card-dark) 75%);
  }
  .product {
    position: absolute; left: 0; top: 225px; width: 100%;
    display: flex; align-items: center; justify-content: center; gap: 14px;
  }
  .product__dot {
    width: 34px; height: 34px; border-radius: 50%;
    background: linear-gradient(160deg, var(--mark-cyan), var(--mark-purple));
  }
  .product__name { font-weight: 500; font-size: 40px; line-height: 48px; color: var(--white); }
  .tagline {
    position: absolute; left: 0; top: 303px; width: 100%;
    text-align: center; font-style: italic; font-weight: 500;
    font-size: 17.5px; color: var(--white);
  }
  .website-row {
    position: absolute; left: 0; top: 340px; width: 100%; height: 24px;
    display: flex; align-items: center; justify-content: center; gap: 8px;
  }
  .website-row__line { width: 130px; height: 2px; flex: none; }
  .website-row__line--left { background: linear-gradient(90deg, transparent, var(--accent-blue)); }
  .website-row__line--right { background: linear-gradient(90deg, var(--accent-blue), transparent); }
  .website-row__node { width: 12px; height: 12px; flex: none; margin: 0 -4px; }
  .website { font-size: 17px; letter-spacing: .4px; color: var(--white); white-space: nowrap; padding: 0 4px; }
</style>
</head>
<body>

<section class="card card--front" aria-label="Business card, contact side">
  <div class="brand">
    <span class="brand__dot"></span>
    <div class="brand__name">Brightloom</div>
  </div>
  <div class="divider"></div>
  <div class="contact">
    <div class="contact__name">Perry Dunmore</div>
    <div class="contact__title">Founder &amp; CEO</div>
    <ul class="contact__list">
      <li class="contact__item">
        <svg class="contact__icon" viewBox="0 0 24 24" aria-hidden="true"><path d="M6.6 10.8a15.1 15.1 0 0 0 6.6 6.6l2.2-2.2c.3-.3.7-.4 1-.2 1.1.4 2.3.6 3.6.6.6 0 1 .4 1 1V20c0 .6-.4 1-1 1C10.6 21 3 13.4 3 4c0-.6.4-1 1-1h3.5c.6 0 1 .4 1 1 0 1.3.2 2.5.6 3.6.1.3 0 .7-.2 1z"/></svg>
        (555)-014-2286
      </li>
      <li class="contact__item">
        <svg class="contact__icon" viewBox="0 0 24 24" aria-hidden="true"><path d="M2 6h20v12H2z M3.5 7.5 12 13l8.5-5.5" fill="none" stroke="#1f1f1f" stroke-width="2"/></svg>
        pdunmore@quillpost-mail.net
      </li>
    </ul>
  </div>
  <svg class="color-band" viewBox="0 0 686 11" preserveAspectRatio="none" aria-hidden="true">
    <defs>
      <linearGradient id="spectrum" x1="0" x2="1">
        <stop offset="0" stop-color="#f7883b"/>
        <stop offset=".2" stop-color="#f0384a"/>
        <stop offset=".45" stop-color="#b23fa6"/>
        <stop offset=".7" stop-color="#6a5cf2"/>
        <stop offset=".9" stop-color="#3aa2f5"/>
        <stop offset="1" stop-color="#2ad8ea"/>
      </linearGradient>
    </defs>
    <polygon points="0,0 451,0 448,11 0,11" fill="url(#spectrum)"/>
    <polygon points="456,0 686,0 686,11 452,11" fill="#1b1b1b"/>
  </svg>
</section>

<section class="card card--back" aria-label="Business card, product side">
  <div class="pattern" role="img" aria-label="Faint repeating brand-symbol pattern across the dark background"></div>
  <div class="product">
    <span class="product__dot"></span>
    <span class="product__name">Glimworld</span>
  </div>
  <p class="tagline">Culturally Immersive Language Learning Games</p>
  <div class="website-row">
    <span class="website-row__line website-row__line--left"></span>
    <svg class="website-row__node" viewBox="0 0 12 12" aria-hidden="true"><circle cx="6" cy="6" r="4.5" fill="none" stroke="#4a7bf0" stroke-width="2"/><circle cx="6" cy="6" r="1.5" fill="#4a7bf0"/></svg>
    <span class="website">www.glimworld-play.com</span>
    <svg class="website-row__node" viewBox="0 0 12 12" aria-hidden="true"><circle cx="6" cy="6" r="4.5" fill="none" stroke="#4a7bf0" stroke-width="2"/><circle cx="6" cy="6" r="1.5" fill="#4a7bf0"/></svg>
    <span class="website-row__line website-row__line--right"></span>
  </div>
</section>

</body>
</html>
```